Business Card design for insurance broker in Denver, CO, USA

I need a business card designed using this logo that was just created. We sell life and disability income insurance to US consumers.
Looking for a professionally designed card to make use of the logo and have something to hand to prospects or new business referral sources. The card could be white, gray, black or whatever you would recommend.

Target Market(s)

US Consumers and other financial professionals that I partner with.

Industry/Entity Type

Insurance Broker

Contact Information for Business Card

Owen T. Farrow, CLU, LUTCF (please note that CLU should have a superscript R in a circle for registered trademark)
President
phone (303) 555-0187
email owen@keelbrookcover.example
4620 W. Halvern Rd, Suite 300, Greenwood Village, CO 80111
Somewhere fit in a tagline saying "Your resource for life, long term care, and disability insurance" (maybe the back if it doesn't fit on the front, your call)

Font styles to use
Sans Serif

Requirements
Must have
• Must have logo in correct blue and gray colors, my name, address, phone, email. Order and placement determined by the designer.
• I just want something that looks a more professional than what I could have done using the business card designer tool on pixelbazaar.example or QuillPress, or any other do-it-yourself tool
• A regular rectangular business card with square corners is preferred
Nice to have
• I included the logos of 2 organizations I belong to (GKLS and WOBCE). They should be small, but visible on the back only. If it doesn’t look good, this is not a requirement, feel free to drop it.
Should not have
• Do not add any colors not already in the logo, except use of black and whites which are okay. If you use the logo on the back and want to make that in all black, gray or white, that may be okay as well.

```html
<!DOCTYPE html>
<html lang="en">
<head>
<meta charset="utf-8">
<title>Keelbrook Insurance Solutions – Business Card</title>
<link rel="stylesheet" href="https://fonts.googleapis.com/css2?family=Montserrat:wght@400;500;600&display=swap">
<style>
  :root {
    --backdrop: #2b2b2b;
    --card: #262626;
    --brand-blue: #2f8fd6;
    --brand-gray: #a9a9a9;
    --ink-white: #f2f2f2;
    --faint: #3a3a3a;
  }
  * { box-sizing: border-box; margin: 0; padding: 0; }
  html, body { width: 1200px; height: 900px; overflow: hidden; }
  body {
    background: var(--backdrop);
    font-family: "Montserrat", sans-serif;
    position: relative;
  }
  .card {
    position: absolute;
    left: 230px;
    width: 740px;
    height: 410px;
    background: var(--card);
    box-shadow: 0 10px 30px rgba(0,0,0,.45);
    overflow: hidden;
  }
  .card--back { top: 30px; }
  .card--front { top: 460px; }

  /* logo lockup */
  .brand {
    display: flex;
    align-items: center;
    gap: 14px;
    color: var(--brand-blue);
    font-weight: 600;
    line-height: 1;
  }
  .brand__dot {
    width: 58px; height: 58px;
    border: 4px solid var(--brand-blue);
    border-radius: 50%;
    flex: none;
  }
  .brand__name { font-size: 30px; letter-spacing: .5px; }
  .brand__name span { display: block; }
  .brand__name span + span { margin-top: 4px; }

  /* back */
  .card--back .brand { position: absolute; left: 50%; top: 95px; transform: translateX(-50%); }
  .back__rule {
    position: absolute; left: 70px; top: 300px;
    width: 440px; height: 3px; background: var(--brand-gray);
  }
  .badges { position: absolute; right: 40px; bottom: 38px; display: flex; gap: 22px; align-items: flex-end; }
  .badge { background: var(--brand-gray); opacity: .8; }
  .badge--round { width: 90px; height: 30px; border-radius: 15px; }
  .badge--tri { width: 54px; height: 40px; clip-path: polygon(50% 0, 100% 100%, 0 100%); }

  /* front */
  .card--front .brand { position: absolute; left: 40px; top: 32px; }
  .card--front .brand__dot { width: 50px; height: 50px; }
  .card--front .brand__name { font-size: 25px; }
  .person { position: absolute; left: 40px; top: 130px; }
  .person__name { color: var(--brand-blue); font-size: 30px; font-weight: 500; letter-spacing: .5px; }
  .person__creds { color: var(--ink-white); font-size: 17px; font-weight: 400; }
  .person__creds sup { font-size: 10px; }
  .person__title { color: var(--ink-white); font-size: 15px; margin-top: 2px; }
  .person__bar { width: 28px; height: 3px; background: var(--brand-blue); margin-top: 10px; }
  .contacts { position: absolute; left: 40px; top: 252px; list-style: none; }
  .contacts li { display: flex; align-items: center; gap: 14px; color: var(--ink-white); font-size: 16px; height: 32px; }
  .contacts svg { width: 18px; height: 18px; fill: var(--brand-blue); flex: none; }
  .tagline {
    position: absolute; right: 40px; top: 40px;
    text-align: right; color: var(--ink-white); font-size: 14px; line-height: 1.45;
    padding-right: 14px; border-right: 3px solid var(--brand-blue);
  }
  .watermark-ring {
    position: absolute; right: 50px; top: 150px;
    width: 230px; height: 230px; border: 10px solid var(--faint); border-radius: 50%;
  }
  .address {
    position: absolute; right: 40px; bottom: 40px;
    text-align: right; color: var(--brand-blue); font-size: 16px; line-height: 1.7;
  }
</style>
</head>
<body>

<section class="card card--back" aria-label="Card back">
  <div class="brand">
    <div class="brand__dot"></div>
    <div class="brand__name"><span>KEELBROOK</span><span>INSURANCE SOLUTIONS</span></div>
  </div>
  <div class="back__rule"></div>
  <div class="badges">
    <div class="badge badge--round" role="img" aria-label="GKLS membership badge"></div>
    <div class="badge badge--tri" role="img" aria-label="WOBCE membership badge"></div>
  </div>
</section>

<section class="card card--front" aria-label="Card front">
  <div class="brand">
    <div class="brand__dot"></div>
    <div class="brand__name"><span>KEELBROOK</span><span>INSURANCE SOLUTIONS</span></div>
  </div>

  <div class="person">
    <p><span class="person__name">OWEN T. FARROW</span> <span class="person__creds">CLU<sup>®</sup>, LUTCF</span></p>
    <p class="person__title">President</p>
    <div class="person__bar"></div>
  </div>

  <ul class="contacts">
    <li>
      <svg viewBox="0 0 24 24" aria-hidden="true"><path d="M6.6 10.8a15.1 15.1 0 0 0 6.6 6.6l2.2-2.2a1 1 0 0 1 1-.25 11.4 11.4 0 0 0 3.6.57 1 1 0 0 1 1 1V20a1 1 0 0 1-1 1A17 17 0 0 1 3 4a1 1 0 0 1 1-1h3.5a1 1 0 0 1 1 1c0 1.25.2 2.45.57 3.57a1 1 0 0 1-.25 1z"/></svg>
      (303) 555-0187
    </li>
    <li>
      <svg viewBox="0 0 24 24" aria-hidden="true"><path d="M2 5h20v14H2z M2 5l10 8 10-8" fill="none" stroke="#2f8fd6" stroke-width="2"/></svg>
      owen@keelbrookcover.example
    </li>
    <li>
      <svg viewBox="0 0 24 24" aria-hidden="true"><circle cx="12" cy="12" r="9" fill="none" stroke="#2f8fd6" stroke-width="2"/><path d="M3 12h18M12 3c3 3 3 15 0 18M12 3c-3 3-3 15 0 18" fill="none" stroke="#2f8fd6" stroke-width="1.6"/></svg>
      www.keelbrookcover.example
    </li>
  </ul>

  <p class="tagline">Your resource for LIFE<br>Long term CARE<br>and DISABILITY INSURANCE</p>

  <div class="watermark-ring" aria-hidden="true"></div>

  <p class="address">4620 W. Halvern Rd, Suite 300<br>Greenwood Village, CO 80111</p>
</section>

</body>
</html>
```